Kelvaro.ch is looking for business card letterhead and envelope C5 with WOW effect

We need a strong business card for our company Kelvaro.ch, logo is available. You want a black or dark background on which the logo Stark r% 26 # 252; appears. Letterhead and envelope in C5 format should be in a similar design, but does not have to be We need a strong business card for our company Kelvaro.ch, logo is available. A black or dark background is desired, on which the logo Stark comes across. The letterhead and the envelope in C5 format should have a similar design.

Target Market(s)

Private customers as well as entrepreneurs

Contact Information for Business Card

E-mail: info@kelvaro-example.ch
Web.www.Kelvaro-example.ch
Tel: +41 ( 0 ) 79 482 6037
Adresse:
Lindenweg 14
9406 Tarnbach

Hier kann man Icons verwenden für Email,Tel und Adressse

Font styles to use
Other font styles liked:
• Dubai,bold

Colors

Designer to choose colors to be used in the design.

Requirements
Must have
• WOW effect
Nice to have
• R% 26 # 252; back business card with our service listings. - VEHICLE LABELING - SHOP WINDOW LABELING - STICKERS AND MUCH MORE ... in red color

```html
<!DOCTYPE html>
<html lang="en">
<head>
<meta charset="utf-8">
<title>Kelvaro.ch – Business Card</title>
<link rel="stylesheet" href="https://fonts.googleapis.com/css2?family=Montserrat:wght@400;500;700&display=swap">
<style>
  :root {
    --page-bg: #0a0a0a;
    --card-bg: #2a2a2b;
    --card-edge: #f2c21b;
    --brand-yellow: #f6c814;
    --text-light: #f2f2f2;
    --emboss-grey: #5c5c5e;
    --service-red: #d4151b;
    --divider-gold: #9a7a12;
  }
  * { box-sizing: border-box; margin: 0; padding: 0; }
  html, body {
    width: 1200px; height: 822px; overflow: hidden;
    background: var(--page-bg);
    font-family: "Montserrat", sans-serif;
  }
  .canvas {
    position: relative; width: 1200px; height: 822px;
    display: flex; align-items: center; justify-content: center; gap: 60px;
  }
  .card {
    position: relative; width: 500px; height: 286px;
    background: var(--card-bg);
    border-bottom: 3px solid var(--card-edge);
    border-left: 2px solid var(--card-edge);
    box-shadow: 0 18px 40px rgba(0,0,0,.7);
  }
  .brand {
    display: flex; align-items: center; gap: 14px;
  }
  .brand-square { width: 34px; height: 34px; }
  .brand-name { font-weight: 700; letter-spacing: .5px; }

  /* front */
  .card-front .brand { position: absolute; left: 120px; top: 70px; }
  .card-front .brand-square { background: var(--brand-yellow); }
  .card-front .brand-name { font-size: 36px; color: var(--text-light); }
  .contact {
    position: absolute; left: 0; right: 0; bottom: 40px;
    text-align: center; color: var(--text-light); font-size: 13px;
  }
  .contact-address { margin-bottom: 8px; }
  .contact-divider {
    width: 90px; height: 1px; background: var(--divider-gold);
    margin: 0 auto 8px;
  }
  .contact-label { color: var(--brand-yellow); font-weight: 700; }
  .contact-web { color: var(--brand-yellow); }

  /* back */
  .card-back { display: flex; flex-direction: column; align-items: center; justify-content: center; gap: 18px; }
  .card-back .brand-square { background: var(--emboss-grey); }
  .card-back .brand-name { font-size: 34px; color: var(--emboss-grey); }
  .services {
    text-align: center; color: var(--service-red);
    font-size: 11px; font-weight: 500; line-height: 1.5; letter-spacing: .3px;
  }
</style>
</head>
<body>
<main class="canvas">
  <section class="card card-front" aria-label="Business card front">
    <div class="brand">
      <span class="brand-square"></span>
      <span class="brand-name">KELVARO.CH</span>
    </div>
    <div class="contact">
      <p class="contact-address">Lindenweg 14, 9406 Tarnbach</p>
      <div class="contact-divider"></div>
      <p class="contact-line">
        <span class="contact-label">P:</span> +41 ( 0 ) 79 482 6037 |
        <span class="contact-label">E:</span> info@kelvaro-example.ch |
        <span class="contact-web">www.Kelvaro-example.ch</span>
      </p>
    </div>
  </section>

  <section class="card card-back" aria-label="Business card back">
    <div class="brand">
      <span class="brand-square"></span>
      <span class="brand-name">KELVARO.CH</span>
    </div>
    <p class="services">VEHICLE LABELING | SHOP WINDOW LABELING<br>STICKERS AND MUCH MORE ...</p>
  </section>
</main>
</body>
</html>
```